Emergency and Referral Vet Hospital promotional sticker design

We're looking at getting some stickers designed that we could give to clients to put on their cars for promotion and advertising. If they could also be suitable for a goodie bag for conference too that would be great. I like the look of water-colour backgrounds, we'll need to include our logo and probably our address (Unit 3/215 Korrinup Road Tallowmere). We also have a hospital motto "... because they're family" if that could somehow be integrated, we only care for small animals (dogs, cats etc) but the design is very open to suggestion. Would love to see what you can create.

Industry/Entity Type

Veterinary

Colors
0054AA
0677BA
7BADD7
CADEEF
E8F1F8
0094D4
00A9DD
6FCCEA
C7EBF8
E9F6FB

Requirements
Nice to have
• Think beach vibes, blues maybe paw print shapes etc

```html
<!DOCTYPE html>
<html lang="en">
<head>
<meta charset="utf-8">
<title>Tidewell Vet Hospital – Sticker</title>
<link rel="stylesheet" href="https://fonts.googleapis.com/css2?family=Outfit:wght@400;600;700&family=Great+Vibes&family=Crimson+Text:wght@700&family=Oswald:wght@600&display=swap">
<style>
  :root {
    --surround: #414141;
    --sky-top: #3db3e3;
    --sky-bottom: #0a8fd6;
    --navy-band: #0054AA;
    --wave-edge: #1b8fd3;
    --deep-blue: #0677BA;
    --pill: #6FCCEA;
    --mist: #E8F1F8;
    --script-ink: #0d3b7a;
    --white: #ffffff;
    --logo-ink: #1a1a1a;
  }
  * { margin: 0; padding: 0; box-sizing: border-box; }
  html, body { width: 1200px; height: 843px; overflow: hidden; background: var(--surround); }
  .sticker {
    position: absolute; left: 50px; top: 56px; width: 1099px; height: 733px;
    overflow: hidden; background: var(--mist);
  }
  .sky {
    position: absolute; left: 0; top: 0; width: 1099px; height: 437px;
    background: linear-gradient(180deg, var(--sky-top), var(--sky-bottom));
  }
  .phone-band {
    position: absolute; left: 0; top: 437px; width: 1099px; height: 133px;
    background: var(--navy-band);
  }
  .photo-wave { position: absolute; left: 0; top: 0; width: 1099px; height: 733px; }
  .headline-lead {
    position: absolute; left: 31px; top: 68px;
    font: 400 39px/1 "Outfit", sans-serif; color: var(--white);
  }
  .headline-script {
    position: absolute; left: 40px; top: 130px;
    font: 400 104px/1 "Great Vibes", cursive; color: var(--script-ink);
  }
  .headline-main {
    position: absolute; left: 38px; top: 250px;
    font: 700 57px/1 "Outfit", sans-serif; color: var(--white); letter-spacing: 0.5px;
  }
  .motto {
    position: absolute; left: 38px; top: 322px;
    font: 700 49px/1 "Crimson Text", serif; color: var(--white);
    text-shadow: 0 3px 8px rgba(0, 40, 90, 0.45);
  }
  .phone {
    position: absolute; left: 50px; top: 468px; display: flex; align-items: center; gap: 16px;
  }
  .phone-icon { width: 64px; height: 64px; }
  .phone-number {
    font: 600 72px/1 "Oswald", sans-serif; color: var(--white); letter-spacing: -1px;
  }
  .brand {
    position: absolute; left: 50px; top: 632px; display: flex; align-items: center; gap: 12px;
  }
  .brand-dot { width: 22px; height: 22px; border-radius: 50%; background: var(--deep-blue); }
  .brand-name { font: 600 34px/1 "Outfit", sans-serif; color: var(--logo-ink); }
  .address-backdrop {
    position: absolute; left: 406px; top: 595px; width: 720px; height: 150px;
    border-radius: 70px 0 0 70px; background: var(--deep-blue);
  }
  .address-pill {
    position: absolute; left: 313px; top: 620px; width: 757px; height: 92px;
    border-radius: 46px; background: var(--pill);
    display: flex; align-items: center; padding-left: 36px; gap: 14px;
  }
  .pin-icon { width: 56px; height: 56px; flex: none; }
  .address-text { font: 600 28px/1 "Outfit", sans-serif; color: var(--white); }
</style>
</head>
<body>
  <main class="sticker">
    <div class="sky"></div>
    <div class="phone-band"></div>

    <svg class="photo-wave" viewBox="0 0 1800 1200" preserveAspectRatio="none">
      <defs>
        <linearGradient id="photoTone" x1="0" y1="0" x2="1" y2="1">
          <stop offset="0" stop-color="#e6e8e8"/>
          <stop offset="0.45" stop-color="#d8c3a8"/>
          <stop offset="0.75" stop-color="#c48a55"/>
          <stop offset="1" stop-color="#eeeeee"/>
        </linearGradient>
      </defs>
      <path d="M1018,0 C1040,150 960,260 880,330 C830,380 830,470 870,540 C930,640 1050,660 1200,655 C1330,650 1420,680 1480,760 C1560,860 1680,925 1800,920 L1800,0 Z"
            fill="none" stroke="var(--wave-edge)" stroke-width="60"/>
      <path role="img" aria-label="Photo of a veterinarian with a stethoscope examining a happy beagle"
            d="M1018,0 C1040,150 960,260 880,330 C830,380 830,470 870,540 C930,640 1050,660 1200,655 C1330,650 1420,680 1480,760 C1560,860 1680,925 1800,920 L1800,0 Z"
            fill="url(#photoTone)"/>
    </svg>

    <p class="headline-lead">Give Your pet</p>
    <p class="headline-script">High Quality</p>
    <h1 class="headline-main">VETERINARY CARE</h1>
    <p class="motto">Because they're family</p>

    <div class="phone">
      <svg class="phone-icon" viewBox="0 0 64 64" aria-hidden="true">
        <circle cx="32" cy="32" r="30" fill="none" stroke="#fff" stroke-width="2.5"/>
        <path d="M24 20c-2 0-4 2-4 5 0 10 9 19 19 19 3 0 5-2 5-4l-5-4-3 3c-4-2-7-5-9-9l3-3-4-5z" fill="#fff"/>
        <path d="M35 22a8 8 0 0 1 7 7M35 17a13 13 0 0 1 12 12" fill="none" stroke="#fff" stroke-width="2.2" stroke-linecap="round"/>
      </svg>
      <span class="phone-number">(08) 9537 2418</span>
    </div>

    <div class="brand">
      <span class="brand-dot"></span>
      <span class="brand-name">tidewell</span>
    </div>

    <div class="address-backdrop"></div>
    <div class="address-pill">
      <svg class="pin-icon" viewBox="0 0 56 56" aria-hidden="true">
        <circle cx="28" cy="28" r="26" fill="none" stroke="#fff" stroke-width="2.5"/>
        <path d="M28 14a10 10 0 0 0-10 10c0 8 10 18 10 18s10-10 10-18a10 10 0 0 0-10-10z" fill="#fff"/>
        <circle cx="28" cy="24" r="3.6" fill="var(--pill)"/>
      </svg>
      <span class="address-text">Unit 3/215 Korrinup Road Tallowmere</span>
    </div>
  </main>
</body>
</html>
```